Animal Eye Clinic needs a Business card

We are a new veterinary ophthalmology practice (Ridgeline Pet Vision Care) and we need a business card designed. We only see animal eyes - we are not a regular veterinary clinic. We already have a logo. We are looking for a professional, good looking business card to hand out to our clients. We are looking for something simple but professional and contemporary. Our logo is likely the only picture/graphic that needs to be on the card.
Updates

Contact Information for Business Card

Delia Vossman, BSc, DVM, MSc, DipACVO
Veterinary Ophthalmologist

Phone: 250.418.3927
Email: ridgelinepetvisioncare@mailbox-example.net
Website: ridgelinepetvisioncare-example.net
Address: 1874 Thornbury Rd
Kelowna, BC, V1X 4M9

Colors

Designer to choose colors to be used in the design.

Requirements
Must have
• Our logo (attached)

```html
<!DOCTYPE html>
<html lang="en">
<head>
<meta charset="utf-8">
<title>Ridgeline Pet Vision Care – Business Card</title>
<link rel="stylesheet" href="https://fonts.googleapis.com/css2?family=Oswald:wght@500&family=Roboto:wght@300;400;500&display=swap">
<style>
  :root {
    --stage: #2b2b2b;
    --card: #262626;
    --card-back: #1f1f1f;
    --pattern-dark: #1a1a1a;
    --pattern-light: #3a3a3a;
    --teal: #1396a8;
    --white: #f2f2f2;
    --muted: #d8d8d8;
    --faint: #303030;
  }
  * { box-sizing: border-box; margin: 0; padding: 0; }
  html, body { width: 1200px; height: 901px; overflow: hidden; }
  body {
    background: var(--stage);
    font-family: "Roboto", Arial, sans-serif;
    color: var(--white);
    position: relative;
  }
  .card {
    position: absolute;
    left: 250px;
    width: 700px;
    height: 400px;
    overflow: hidden;
  }
  .card--back { top: 30px; background: var(--card-back); }
  .card--front { top: 471px; background: var(--card); }

  .pattern-area {
    position: absolute; inset: 0;
    background: linear-gradient(115deg, var(--pattern-dark) 0%, var(--pattern-dark) 45%, var(--pattern-light) 100%);
  }

  .brand { position: absolute; display: flex; align-items: center; gap: 12px; }
  .brand__dot {
    width: 46px; height: 46px; border-radius: 50%;
    background: var(--teal); flex: none;
  }
  .brand__name {
    font-family: "Roboto", Arial, sans-serif;
    font-weight: 500;
    color: var(--teal);
    text-transform: uppercase;
    line-height: 1.1;
  }
  .card--back .brand { left: 390px; top: 250px; }
  .card--back .brand__name { font-size: 22px; }

  .watermark-circle {
    position: absolute; left: 110px; top: 60px;
    width: 330px; height: 330px; border-radius: 50%;
    background: var(--faint);
  }
  .card--front .brand { left: 40px; top: 120px; }
  .card--front .brand__name { font-size: 21px; }

  .divider {
    position: absolute; left: 312px; top: 100px;
    width: 2px; height: 125px; background: #888;
  }
  .contact { position: absolute; left: 334px; top: 96px; width: 350px; }
  .contact__name {
    font-family: "Oswald", "Arial Narrow", sans-serif;
    font-weight: 500; color: var(--teal);
    font-size: 20px; letter-spacing: 0.3px; text-transform: uppercase;
  }
  .contact__title { font-size: 17px; font-weight: 400; color: var(--white); margin-bottom: 12px; }
  .contact__row {
    display: flex; align-items: center; gap: 8px;
    font-size: 15px; font-weight: 400; color: var(--white); margin-top: 4px;
    white-space: nowrap;
  }
  .contact__row svg { width: 13px; height: 13px; flex: none; fill: var(--teal); }
  .contact__web { color: var(--teal); }

  .address {
    position: absolute; left: 0; right: 0; top: 320px;
    text-align: center; font-size: 18px; font-weight: 400; color: var(--muted);
  }
  .band {
    position: absolute; left: 0; right: 0; bottom: 0;
    height: 12px; background: var(--teal);
  }
</style>
</head>
<body>

  <section class="card card--back">
    <div class="pattern-area" role="img" aria-label="Repeating pattern of the clinic's logo mark in dark tones fading lighter to the right"></div>
    <div class="brand">
      <span class="brand__dot"></span>
      <span class="brand__name">Ridgeline<br>Pet Vision Care</span>
    </div>
  </section>

  <section class="card card--front">
    <div class="watermark-circle" aria-hidden="true"></div>
    <div class="brand">
      <span class="brand__dot"></span>
      <span class="brand__name">Ridgeline<br>Pet Vision Care</span>
    </div>
    <div class="divider"></div>
    <div class="contact">
      <p class="contact__name">Delia Vossman, BSc, DVM, MSc, DipACVO</p>
      <p class="contact__title">Veterinary Ophthalmologist</p>
      <p class="contact__row">
        <svg viewBox="0 0 24 24" aria-hidden="true"><path d="M6.6 10.8a15.1 15.1 0 0 0 6.6 6.6l2.2-2.2c.3-.3.7-.4 1-.2 1.1.4 2.3.6 3.6.6.6 0 1 .4 1 1V20c0 .6-.4 1-1 1A17 17 0 0 1 3 4c0-.6.4-1 1-1h3.5c.6 0 1 .4 1 1 0 1.3.2 2.5.6 3.6.1.3 0 .7-.2 1z"/></svg>
        250.418.3927
      </p>
      <p class="contact__row">
        <svg viewBox="0 0 24 24" aria-hidden="true"><path d="M2 5h20v14H2z M2 5l10 8 10-8" /></svg>
        ridgelinepetvisioncare@mailbox-example.net
      </p>
      <p class="contact__row">
        <svg viewBox="0 0 24 24" aria-hidden="true"><circle cx="12" cy="12" r="10"/></svg>
        <span>www.<span class="contact__web">ridgelinepetvisioncare-example</span>.net</span>
      </p>
    </div>
    <p class="address">1874 Thornbury Rd, Kelowna, BC, V1X 4M9</p>
    <div class="band"></div>
  </section>

</body>
</html>
```